Marrowfield Air Business Card Design

Design new, 2 sides, business cards for a residential and light commercial heating, air conditioning contractor.

Target Market(s)

Homeowners, small businesses

Industry/Entity Type

Business

Contact Information for Business Card

Dominic Westerhall
Phone - 862-415-2736
Email
Address - PO box 518
Brightwater NJ 07912
Website - www.HarborBreezeLLC.example

Requirements
Must have
• logo, company colors, standard size with no die cut, so I can use nova stamp

```html
<!DOCTYPE html>
<html lang="en">
<head>
<meta charset="utf-8">
<title>Marrowfield Air Business Card</title>
<link href="https://fonts.googleapis.com/css2?family=Oswald:wght@400;500&family=Questrial&display=swap" rel="stylesheet">
<style>
  :root {
    --brand-red: #9e1f32;
    --brand-orange: #f7941d;
    --ink: #4a4a4a;
    --paper: #ffffff;
    --backdrop: #ebe8e4;
  }
  * { box-sizing: border-box; margin: 0; padding: 0; }
  html, body { width: 1200px; height: 987px; overflow: hidden; }
  body { background: var(--backdrop); position: relative; font-family: "Questrial", sans-serif; }

  .card {
    position: absolute;
    left: 293px;
    width: 615px;
    height: 350px;
    box-shadow: 0 2px 6px rgba(0,0,0,0.18);
  }
  .card--front { top: 130px; background: var(--paper); }
  .card--back { top: 506px; background: var(--brand-red); }

  .brand-name {
    position: absolute;
    font-family: "Oswald", sans-serif;
    font-weight: 500;
    text-transform: uppercase;
    letter-spacing: 1px;
    white-space: nowrap;
    display: flex;
    align-items: center;
    gap: 12px;
  }
  .brand-name__dot {
    width: 14px; height: 14px; border-radius: 50%;
    background: var(--brand-orange);
  }
  .card--front .brand-name {
    left: 0; right: 0; top: 66px;
    justify-content: center;
    font-size: 46px;
    color: var(--brand-red);
  }
  .card--back .brand-name {
    right: 36px; top: 234px;
    font-size: 36px;
    color: var(--brand-orange);
  }
  .card--back .brand-name__dot { background: var(--paper); }

  .title-band {
    position: absolute;
    left: 0; top: 182px;
    width: 100%; height: 57px;
    background: var(--brand-red);
  }
  .title-ribbon { position: absolute; left: 30px; top: 7px; }
  .title-line {
    position: absolute;
    left: 0; right: 0; top: 0; height: 57px;
    display: flex; align-items: center; justify-content: center;
    font-family: "Oswald", sans-serif;
    color: var(--paper);
    gap: 8px;
  }
  .title-line__name { font-size: 27px; font-weight: 400; }
  .title-line__role { font-size: 17px; font-weight: 400; }

  .contact {
    position: absolute;
    font-size: 16px;
    color: var(--ink);
    line-height: 23px;
  }
  .contact--left { left: 40px; top: 265px; }
  .contact--right { right: 31px; top: 262px; text-align: right; }
  .contact__row { display: flex; align-items: center; gap: 7px; }
  .contact--right .contact__row { justify-content: flex-end; }
  .icon { width: 15px; height: 15px; fill: var(--brand-orange); flex: none; }
</style>
</head>
<body>

<section class="card card--front">
  <div class="brand-name"><span class="brand-name__dot"></span>Marrowfield Air</div>

  <div class="title-band">
    <svg class="title-ribbon" width="556" height="43" viewBox="0 0 556 43">
      <polygon points="0,0 556,0 536,21.5 556,43 0,43 20,21.5" fill="var(--brand-orange)"/>
    </svg>
    <div class="title-line">
      <span class="title-line__name">Dominic Westerhall</span>
      <span class="title-line__role">- CEO/Founder</span>
    </div>
  </div>

  <div class="contact contact--left">
    <div class="contact__row">
      <svg class="icon" viewBox="0 0 24 24"><path d="M6.6 10.8a15.1 15.1 0 0 0 6.6 6.6l2.2-2.2c.3-.3.7-.4 1-.2 1.1.4 2.3.6 3.6.6.6 0 1 .4 1 1V20c0 .6-.4 1-1 1C10.6 21 3 13.4 3 4c0-.6.4-1 1-1h3.5c.6 0 1 .4 1 1 0 1.3.2 2.5.6 3.6.1.3 0 .7-.2 1z"/></svg>
      <span>862 415 2736</span>
    </div>
    <div class="contact__row">PO box 518</div>
    <div class="contact__row">Brightwater NJ 07912</div>
  </div>

  <div class="contact contact--right">
    <div class="contact__row">
      <span>862 507 3318</span>
      <svg class="icon" viewBox="0 0 24 24"><path d="M7 1h10a2 2 0 0 1 2 2v18a2 2 0 0 1-2 2H7a2 2 0 0 1-2-2V3a2 2 0 0 1 2-2zm0 3v14h10V4zm5 15.5a1.2 1.2 0 1 0 0 2.4 1.2 1.2 0 0 0 0-2.4z"/></svg>
    </div>
    <div class="contact__row">
      <span>862 415 2790</span>
      <svg class="icon" viewBox="0 0 24 24"><path d="M6 2h12v6H6zM3 9h18a1 1 0 0 1 1 1v8h-4v4H6v-4H2v-8a1 1 0 0 1 1-1zm5 7v4h8v-4z"/></svg>
    </div>
    <div class="contact__row">
      <span>dominic@marrowfieldair.example</span>
      <svg class="icon" viewBox="0 0 24 24"><path d="M2 5h20v14H2zm2 2v.5l8 5.5 8-5.5V7l-8 5.3z"/></svg>
    </div>
  </div>
</section>

<section class="card card--back">
  <div class="brand-name"><span class="brand-name__dot"></span>Marrowfield Air</div>
</section>

</body>
</html>
```